K7 Electrical Services Ltd Web design

I require a web site for my new electrical contracting company. We are customer service orientated. Offering high value electrical installations, design and maintenance. Focused on custom residential and commercial upgrading. Lighting design and application are paramount in our company's services. Industry leading product use and integration are always on the forefront with our customer client services. As well as energy efficiency.

Target Market(s)

Homebuilders, General Contractors, Property management companies, clients, individuals,

Industry/Entity Type

Electric Company

Coding

Coded - Design and coding required

Number of Pages Required

3 page

Requirements
Must have
• Classic, modern, edgy but not trendy . Appeals to the masse.
• 3 page
• home page
• about page
• gallery page
• ability to contact from the webiste
Nice to have
• open to all types of designs that are relative to the construction industry.
• Black, Grey, metallic ice blue and deep purple colours from the logo.
Should not have
• anything cheesy with cartoon light bulb images.

```html
<!DOCTYPE html>
<html lang="en">
<head>
<meta charset="utf-8">
<title>K7 Electrical Services Ltd</title>
<link rel="stylesheet" href="https://fonts.googleapis.com/css2?family=Raleway:wght@400;600;700;800&family=Lato:ital,wght@0,400;0,700;1,400&display=swap">
<style>
  :root{
    --purple:#5b2d91;
    --purple-band:#5a3a9e;
    --ink:#222222;
    --text:#6b6b6b;
    --muted:#8a8a8a;
    --line:#e3e3e3;
    --footer:#333333;
    --footer-line:#4a4a4a;
    --white:#ffffff;
    --link:#2d6fb4;
  }
  *{box-sizing:border-box;margin:0;padding:0}
  html,body{width:1200px;height:3396px;overflow:hidden;background:var(--white)}
  body{position:relative;font-family:'Lato',sans-serif;color:var(--text)}
  .abs{position:absolute}
  h1,h2,h3,h4{font-family:'Raleway',sans-serif;color:var(--ink)}

  /* header */
  .brand{left:100px;top:64px;font-family:'Raleway',sans-serif;color:var(--purple);font-weight:700;font-size:24px;line-height:30px;white-space:nowrap}
  .nav{top:40px;left:618px;font-family:'Raleway',sans-serif;font-size:13px;font-weight:700;color:var(--white)}
  .nav a{position:absolute;color:var(--white);text-decoration:none;white-space:nowrap}

  /* hero */
  .hero-art{left:0;top:0}
  .hero-title{left:100px;top:384px;font-size:31px;font-weight:700;line-height:44px;text-transform:uppercase;letter-spacing:.5px;color:var(--ink)}
  .hero-sub{left:100px;top:528px;font-family:'Raleway',sans-serif;font-size:19px;font-weight:700;color:#555}

  /* welcome */
  .welcome-photo{left:100px;top:792px;width:337px;height:317px;border-radius:40px;background:linear-gradient(135deg,#dfe4ea,#9fb0c8 55%,#2d4d8f)}
  .welcome-title{left:496px;top:786px;font-size:30px;font-weight:700}
  .body-copy{font-size:12px;line-height:21px;color:var(--muted)}
  .welcome-copy{left:496px;top:834px;width:620px}
  .sub-head{font-family:'Raleway',sans-serif;font-size:20px;font-weight:700;color:var(--ink)}
  .res-head{left:496px;top:928px}
  .com-head{left:820px;top:928px}
  .res-copy{left:496px;top:964px;width:296px}
  .com-copy{left:820px;top:964px;width:296px}
  .btn{left:496px;top:1067px;width:138px;height:40px;border-radius:20px;background:var(--purple);color:var(--white);font-family:'Raleway',sans-serif;font-size:12px;font-weight:700;display:flex;align-items:center;justify-content:center}

  /* video */
  .video{left:0;top:1195px;width:1200px;height:345px;background:linear-gradient(100deg,#39404a,#1f242b 45%,#4a4238 75%,#2c3036)}
  .video-title{left:0;top:1276px;width:1200px;text-align:center;color:var(--white);font-size:29px;font-weight:700;letter-spacing:.5px}
  .video-sub{left:0;top:1344px;width:1200px;text-align:center;color:#e8e8e8;font-size:19px}

  /* services */
  .svc-lead{left:100px;top:1625px;width:224px;height:234px;background:var(--purple);color:var(--white);font-family:'Raleway',sans-serif;font-size:18px;font-weight:700;line-height:31px;text-align:center;display:flex;align-items:center;justify-content:center}
  .svc-card{top:1625px;width:226px;height:234px;border:1px solid var(--line);background:var(--white);box-shadow:0 2px 6px rgba(0,0,0,.06);text-align:center;padding-top:22px}
  .svc-card svg{display:block;margin:0 auto}
  .svc-card h3{font-size:12.5px;font-weight:700;margin-top:22px;text-transform:uppercase}
  .svc-card p{font-size:12px;line-height:21px;color:var(--muted);margin:12px auto 0;width:180px}

  /* testimonials */
  .testi-band{left:0;top:1947px;width:1200px;height:466px;background:var(--purple-band)}
  .testi-title{left:0;top:2014px;width:1200px;text-align:center;color:var(--white);font-size:30px;font-weight:700}
  .testi-card{top:2108px;width:324px;height:179px;background:var(--white);border-radius:22px;padding:22px 22px 0 22px}
  .testi-card p{font-style:italic;font-size:11.5px;line-height:22px;color:var(--text)}
  .testi-card .who{text-align:right;font-family:'Raleway',sans-serif;font-weight:700;font-size:12px;color:var(--ink);margin-top:4px}
  .avatar{top:2244px;width:84px;height:84px;border-radius:50%;border:4px solid var(--white);background:linear-gradient(160deg,#c9b8a6,#6d5a4c)}

  /* blog */
  .blog-title{left:0;top:2494px;width:1200px;text-align:center;font-size:30px;font-weight:700}
  .blog-photo{top:2590px;width:222px;height:236px;border:1px solid var(--line)}
  .blog-photo.one{left:100px;background:linear-gradient(135deg,#7b8490,#c9772e 55%,#3c4652)}
  .blog-photo.two{left:616px;background:linear-gradient(135deg,#b6c0ca,#5a6673 50%,#d2c9b6)}
  .post{width:250px}
  .post h3{font-size:16px;font-weight:600;color:var(--ink)}
  .post .meta{margin-top:14px;font-size:12px;color:var(--muted);display:flex;gap:18px;align-items:center}
  .post .meta span{display:flex;align-items:center;gap:6px}
  .post .excerpt{margin-top:12px;font-size:12.5px;line-height:22px;color:var(--muted)}
  .post .acts{margin-top:12px;font-size:12px;color:var(--link);display:flex;gap:18px}
  .post .acts span{display:flex;align-items:center;gap:6px}

  /* footer */
  .footer{left:0;top:2975px;width:1200px;height:421px;background:var(--footer)}
  .foot-badge{left:550px;top:2911px;width:100px;height:100px;transform:rotate(45deg);background:var(--white);border:2px solid var(--footer)}
  .foot-badge-text{left:530px;top:2953px;width:140px;text-align:center;font-family:'Raleway',sans-serif;font-weight:700;color:var(--purple);font-size:13px;line-height:16px;white-space:nowrap}
  .foot-head{top:3060px;color:var(--white);font-size:17px;font-weight:700;text-transform:uppercase}
  .foot-copy{font-size:12px;line-height:21px;color:#cfcfcf}
  .news-input{left:401px;top:3112px;width:200px;height:36px;background:var(--white);font-size:12px;color:#999;padding:0 12px;display:flex;align-items:center}
  .news-btn{left:401px;top:3171px;width:135px;height:40px;background:var(--purple);color:var(--white);font-size:12px;font-weight:700;display:flex;align-items:center;justify-content:center}
  .contact-row{left:706px;display:flex;gap:16px;align-items:flex-start}
  .social{left:978px;display:flex;align-items:center;gap:20px;font-size:12px;color:#e0e0e0}
  .social i{display:block;width:36px;height:36px;border-radius:50%}
  .rule{left:100px;top:3328px;width:1000px;height:1px;background:var(--footer-line)}
  .copyright{left:0;top:3354px;width:1200px;text-align:center;font-size:12px;color:#cfcfcf}
</style>
</head>
<body>

<svg class="abs hero-art" width="1200" height="713" viewBox="0 0 1200 713" role="img" aria-label="Smiling electrician in a hard hat and safety vest in front of a substation">
  <defs>
    <linearGradient id="heroFill" x1="0" y1="0" x2="1" y2="1">
      <stop offset="0" stop-color="#8c949c"/>
      <stop offset=".45" stop-color="#b9bfc5"/>
      <stop offset=".75" stop-color="#e0812e"/>
      <stop offset="1" stop-color="#6c5b4e"/>
    </linearGradient>
  </defs>
  <path d="M560 0 L1200 0 L1200 450 L950 690 Q928 712 905 690 L392 205 Q372 186 392 166 Z" fill="url(#heroFill)"/>
  <circle cx="905" cy="645" r="5" fill="#fff"/>
  <circle cx="926" cy="622" r="5" fill="#fff"/>
  <circle cx="947" cy="600" r="5" fill="#fff"/>
  <circle cx="968" cy="578" r="5" fill="#fff" opacity=".6"/>
</svg>

<div class="abs brand">K7 Electrical Services</div>

<nav class="abs nav">
  <a style="left:0">HOME</a>
  <a style="left:75px">ABOUT US</a>
  <a style="left:174px">SERVICES</a>
  <a style="left:272px">BLOG</a>
  <a style="left:342px">CONTACT US</a>
  <svg style="position:absolute;left:475px;top:0" width="14" height="14" viewBox="0 0 14 14"><circle cx="6" cy="6" r="4.5" fill="none" stroke="#fff" stroke-width="2"/><line x1="9.5" y1="9.5" x2="13" y2="13" stroke="#fff" stroke-width="2"/></svg>
</nav>

<h1 class="abs hero-title">Offering high value<br>electrical installations,<br>design and maintenance</h1>
<p class="abs hero-sub">Sed ut perspiciatis unde omnis iste natus error</p>

<div class="abs welcome-photo" role="img" aria-label="Two electricians in hard hats working on a wall panel"></div>
<h2 class="abs welcome-title">Welcome TO K7 Electrical</h2>
<p class="abs body-copy welcome-copy">Neque porro quisquam est, qui dolorem ipsum quia dolor sit amet, consectetur, adipisci velit, sed quia non numquam eius modi tempora incidunt ut labore et dolore magnam aliquam quaerat voluptatem. Ut enim ad minima veniam, quis nostrum exercitationem ullam corporis suscipit laboriosam, nisi ut aliquid</p>
<h3 class="abs sub-head res-head">1.Residential</h3>
<h3 class="abs sub-head com-head">2.Commercial</h3>
<p class="abs body-copy res-copy">Quis autem vel eum iure reprehenderit voluptate velit esse quam nihil molestiae consequatur, illum qui dolorem eum fugiat quo voluptas nulla pariatur</p>
<p class="abs body-copy com-copy">At vero eos et accusamus et iusto odio dignissimos ducimus qui blanditiis praesentium voluptatum deleniti atque corrupti quos dolores et quas</p>
<div class="abs btn">LEARN MORE &gt;&gt;</div>

<div class="abs video" role="img" aria-label="Two electricians in hard hats inspecting a switchboard"></div>
<h2 class="abs video-title">WATCH VIDEO</h2>
<p class="abs video-sub">Quo minus quod maxime placeat facere possimus, omnis voluptas</p>
<svg class="abs" style="left:578px;top:1406px" width="44" height="44" viewBox="0 0 44 44"><circle cx="22" cy="22" r="21" fill="#fff"/><path d="M17 13 L31 22 L17 31 Z" fill="#222"/></svg>

<div class="abs svc-lead">OUR<br>MAIN<br>SERVICES</div>

<div class="abs svc-card" style="left:358px">
  <svg width="76" height="76" viewBox="0 0 76 76" fill="none" stroke="#111" stroke-width="3" stroke-linejoin="round">
    <path d="M38 4 L26 72 M38 4 L50 72 M20 22 H56 M14 36 H62 M30 50 H46 M29 22 L47 36 M47 22 L29 36 M32 36 L44 50 M44 36 L32 50 M28 60 L48 72 M48 60 L28 72 M28 60 H48"/>
  </svg>
  <h3>Electrical Installations</h3>
  <p>Temporibus autem quibusdam et eaque officiis debitis aut rerum necessitatibus saepe eveniet</p>
</div>

<div class="abs svc-card" style="left:616px">
  <svg width="76" height="76" viewBox="0 0 76 76" fill="none" stroke="#111" stroke-width="3" stroke-linejoin="round">
    <rect x="8" y="14" width="52" height="54" rx="4"/>
    <rect x="16" y="22" width="36" height="38"/>
    <path d="M40 48 L66 8 L72 12 L46 52 L38 56 Z"/>
    <path d="M22 52 Q30 40 36 48"/>
  </svg>
  <h3>Design</h3>
  <p>Temporibus autem quibusdam et eaque officiis debitis aut rerum necessitatibus saepe eveniet</p>
</div>

<div class="abs svc-card" style="left:874px">
  <svg width="76" height="76" viewBox="0 0 76 76" fill="none" stroke="#111" stroke-width="3" stroke-linejoin="round" stroke-linecap="round">
    <path d="M12 64 L48 28 M48 28 Q44 14 56 8 L52 18 L58 24 L68 20 Q62 32 48 28"/>
    <path d="M10 10 L18 8 L22 16 L64 58 L58 64 L16 22 L8 18 Z"/>
    <circle cx="12" cy="64" r="4"/>
  </svg>
  <h3>Maintenance</h3>
  <p>Temporibus autem quibusdam et eaque officiis debitis aut rerum necessitatibus saepe eveniet</p>
</div>

<section class="abs testi-band"></section>
<h2 class="abs testi-title">TESTIMONIALS</h2>
<svg class="abs" style="left:44px;top:2168px" width="20" height="26" viewBox="0 0 20 26"><path d="M16 2 L5 13 L16 24" fill="none" stroke="#fff" stroke-width="3"/></svg>
<svg class="abs" style="left:1136px;top:2168px" width="20" height="26" viewBox="0 0 20 26"><path d="M4 2 L15 13 L4 24" fill="none" stroke="#fff" stroke-width="3"/></svg>

<div class="abs testi-card" style="left:100px">
  <p>"Sed ut perspiciatis unde omnis iste natus error sit voluptatem accusantium doloremque laudantium, totam rem aperiam, eaque ipsa quae"</p>
  <div class="who">- Author Name &amp; Location</div>
</div>
<div class="abs testi-card" style="left:437px">
  <p>"Sed ut perspiciatis unde omnis iste natus error sit voluptatem accusantium doloremque laudantium, totam rem aperiam, eaque ipsa quae"</p>
  <div class="who">- Author Name &amp; Location</div>
</div>
<div class="abs testi-card" style="left:774px">
  <p>"Sed ut perspiciatis unde omnis iste natus error sit voluptatem accusantium doloremque laudantium, totam rem aperiam, eaque ipsa quae"</p>
  <div class="who">- Author Name &amp; Location</div>
</div>
<div class="abs avatar" style="left:219px" role="img" aria-label="Client portrait"></div>
<div class="abs avatar" style="left:557px" role="img" aria-label="Client portrait"></div>
<div class="abs avatar" style="left:894px" role="img" aria-label="Client portrait"></div>

<h2 class="abs blog-title">LATEST BLOG</h2>
<div class="abs blog-photo one" role="img" aria-label="Electrician in orange overalls working at a control cabinet"></div>
<div class="abs blog-photo two" role="img" aria-label="Engineers in hard hats reviewing plans on site"></div>

<article class="abs post" style="left:342px;top:2596px">
  <h3>Consequuntur magni dolores</h3>
  <div class="meta">
    <span><svg width="11" height="11" viewBox="0 0 11 11"><circle cx="5.5" cy="3" r="2.5" fill="var(--purple)"/><path d="M0.5 11 Q5.5 4 10.5 11 Z" fill="var(--purple)"/></svg>By Someone</span>
    <span><svg width="13" height="11" viewBox="0 0 13 11"><path d="M1 1 H12 V8 H5 L2 10.5 V8 H1 Z" fill="var(--purple)"/></svg>Comment</span>
  </div>
  <p class="excerpt">Lorem ipsum dolor sit amet, consectetur adipiscing elit, sed do eiusmod tempor qert incididunt labore et dolore magna aliqua.Enim ad minim veniam, poigy sed nostrudexercitation ullamco laboris</p>
  <div class="acts">
    <span><svg width="11" height="11" viewBox="0 0 11 11"><path d="M0 5 H2.5 V11 H0 Z M3.5 5 L6 0 Q8 0 7 4 H11 L9.5 11 H3.5 Z" fill="var(--link)"/></svg>Like</span>
    <span><svg width="12" height="11" viewBox="0 0 12 11"><path d="M7 0 L12 5 L7 10 V7 Q2 7 0 11 Q1 3 7 3 Z" fill="var(--link)"/></svg>Share</span>
    <span><svg width="13" height="11" viewBox="0 0 13 11"><path d="M1 1 H12 V8 H5 L2 10.5 V8 H1 Z" fill="var(--link)"/></svg>Comment</span>
  </div>
</article>

<article class="abs post" style="left:856px;top:2596px">
  <h3>Ut enim ad minima veniam</h3>
  <div class="meta">
    <span><svg width="11" height="11" viewBox="0 0 11 11"><circle cx="5.5" cy="3" r="2.5" fill="var(--purple)"/><path d="M0.5 11 Q5.5 4 10.5 11 Z" fill="var(--purple)"/></svg>By Someone</span>
    <span><svg width="13" height="11" viewBox="0 0 13 11"><path d="M1 1 H12 V8 H5 L2 10.5 V8 H1 Z" fill="var(--purple)"/></svg>Comment</span>
  </div>
  <p class="excerpt">Lorem ipsum dolor sit amet, consectetur adipiscing elit, sed do eiusmod tempor qert incididunt labore et dolore magna aliqua.Enim ad minim veniam, poigy sed nostrudexercitation ullamco laboris</p>
  <div class="acts">
    <span><svg width="11" height="11" viewBox="0 0 11 11"><path d="M0 5 H2.5 V11 H0 Z M3.5 5 L6 0 Q8 0 7 4 H11 L9.5 11 H3.5 Z" fill="var(--link)"/></svg>Like</span>
    <span><svg width="12" height="11" viewBox="0 0 12 11"><path d="M7 0 L12 5 L7 10 V7 Q2 7 0 11 Q1 3 7 3 Z" fill="var(--link)"/></svg>Share</span>
    <span><svg width="13" height="11" viewBox="0 0 13 11"><path d="M1 1 H12 V8 H5 L2 10.5 V8 H1 Z" fill="var(--link)"/></svg>Comment</span>
  </div>
</article>

<footer class="abs footer"></footer>
<div class="abs foot-badge"></div>
<div class="abs foot-badge-text">K7 Electrical</div>

<h4 class="abs foot-head" style="left:100px">About Us</h4>
<p class="abs foot-copy" style="left:100px;top:3106px;width:250px">Duis aute irure dolor in reprehenderit voluptate velit esse cillum dolore eu fugiat nulla pariatur. Excepteur sint occaecat cupidatat non proident, sunt in culpa qui officia deserunt mollit anim id est laborum</p>

<h4 class="abs foot-head" style="left:401px">Newsletter</h4>
<div class="abs news-input">Email ID</div>
<div class="abs news-btn">SUBSCRIBE</div>

<h4 class="abs foot-head" style="left:706px">Contact Us</h4>
<div class="abs contact-row" style="top:3108px">
  <svg width="12" height="12" viewBox="0 0 12 12" style="margin-top:4px"><path d="M12 0 L0 5 L5 7 L7 12 Z" fill="#fff"/></svg>
  <p class="foot-copy">#233 Street Name,Building Name<br>Location,Zipcode.</p>
</div>
<div class="abs contact-row" style="top:3174px">
  <svg width="12" height="12" viewBox="0 0 12 12" style="margin-top:4px"><path d="M2 0 L5 0 L6 3 L4 4.5 Q5.5 7 7.5 8 L9 6 L12 7 L12 10 Q11 12 9 12 Q1 10 0 3 Q0 1 2 0 Z" fill="#fff"/></svg>
  <p class="foot-copy">555-0148-2263</p>
</div>
<div class="abs contact-row" style="top:3224px">
  <svg width="12" height="12" viewBox="0 0 12 12" style="margin-top:5px"><rect x="0" y="1" width="12" height="9" fill="#fff"/><path d="M0 1 L6 6 L12 1" fill="none" stroke="#333" stroke-width="1.2"/></svg>
  <p class="foot-copy">Email Us</p>
</div>

<h4 class="abs foot-head" style="left:978px">Follow Us</h4>
<div class="abs social" style="top:3106px"><i style="background:#1d5d8c"></i>Linkface</div>
<div class="abs social" style="top:3158px"><i style="background:#2ba3dd"></i>Chirper</div>
<div class="abs social" style="top:3210px"><i style="background:#d9472f"></i>Circles Plus</div>
<div class="abs social" style="top:3262px"><i style="background:#c4201d"></i>Vidtube</div>

<div class="abs rule"></div>
<p class="abs copyright">Copyrights © 2018 K7 Electrical . Allrights Reserved.</p>

</body>
</html>
```